Website Design for Landscaping/Concrete Company

I need a website that is informative about what my company does and also offers before and after pictures of completed work. I already have a logo. The website must say "FREE ESTIMATES" somewhere and list a phone number. I would like to stick with the logo colors or similar (black and lime green).
Services Offered by Tomlet Builders:
Landscaping
Mowing
Concrete
Sidewalks
Brush Removal
Land Beautification

Please list the company name in large letters TOMLET BUILDERS
and also the contact information in large font.

Right now I am looking for a somewhat coverpage for my website. I don't have a lot of information for people to point and click on yet. Id like to get a coverpage to get my name out and then have a designer come back in a few months and update with more pictures and information.
Updates

If allowed please submit projects after due date. I made a mistake and only posted for one day. Thanks.

Coding

Coded - Design and coding required

```html
<!DOCTYPE html>
<html lang="en">
<head>
<meta charset="utf-8">
<title>Tomlet Builders — Landscaping &amp; Concrete</title>
<link rel="stylesheet" href="https://fonts.googleapis.com/css2?family=Oswald:wght@400;500;600&family=Montserrat:ital,wght@0,400;0,500;0,600;0,700;1,400&display=swap">
<style>
:root{
  --lime:#8db520;
  --lime-dark:#7a9e16;
  --lime-soft:#b9d36a;
  --ink:#1c1c1c;
  --text:#6d6d6d;
  --pale:#f1f3e8;
  --white:#ffffff;
  --orange:#ea7a3c;
  --gold:#f2b01e;
  --footer:#111111;
}
*{margin:0;padding:0;box-sizing:border-box}
html,body{width:1200px;height:5080px;overflow:hidden;background:var(--white)}
body{font-family:"Montserrat",sans-serif;color:var(--ink);position:relative}
.abs{position:absolute}
.heading{font-family:"Oswald",sans-serif;font-weight:500;text-transform:uppercase;color:var(--ink);letter-spacing:.3px}
.eyebrow{font-size:15px;font-weight:600;color:var(--lime-dark);text-transform:uppercase;letter-spacing:.3px}
.center{left:0;width:1200px;text-align:center}
.on-green{color:var(--white)}
.body-copy{font-size:12.5px;line-height:26.5px;color:var(--text)}
.btn{display:flex;align-items:center;justify-content:center;background:var(--lime);color:var(--white);font-size:13px;font-weight:600;text-transform:uppercase;border-radius:3px}

/* header */
.site-header{top:0;left:0;width:1200px;height:93px;background:var(--white)}
.brand{left:108px;top:22px;display:flex;align-items:center;gap:8px}
.brand-mark{width:20px;height:20px;background:var(--ink)}
.brand-name{font-weight:700;font-size:14px;line-height:17px;color:var(--ink);width:100px}
.nav{top:59px;left:0;width:1200px;height:22px}
.nav a{position:absolute;transform:translateX(-50%);font-size:14px;font-weight:500;color:var(--ink);text-decoration:none;text-transform:uppercase}
.nav a.active{color:var(--lime)}
.estimates{left:804px;top:8px;display:flex;align-items:center;gap:8px}
.estimates .phone-dot{width:34px;height:34px;border-radius:50%;background:var(--lime);display:flex;align-items:center;justify-content:center}
.estimates small{display:block;font-size:9.5px;font-weight:700;color:var(--ink)}
.estimates strong{display:block;font-size:19px;font-weight:700;color:var(--lime);line-height:20px}
.header-divider{left:980px;top:8px;width:1px;height:40px;background:#cfcfcf}
.social-dot{top:14px;width:27px;height:27px;border-radius:50%;border:1px solid #9c9c9c}

/* hero */
.hero{top:93px;left:0;width:1200px;height:611px;background:linear-gradient(180deg,#3e6a24 0%,#5e8f2c 30%,#7ea94a 55%,#a8a08a 75%,#6c8c3c 100%)}
.hero-shade{inset:0;background:rgba(0,0,0,.18)}
.hero-title{top:200px;font-family:"Oswald",sans-serif;font-weight:500;font-size:78px;color:var(--white);letter-spacing:1px;line-height:1}
.hero-sub{top:291px;font-size:14px;line-height:29px;color:var(--white)}
.hero-btn{left:530px;top:382px;width:137px;height:37px;border:1px solid var(--white);font-size:12.5px}
.hero-arrow{top:290px;width:30px;height:30px;border-radius:50%;border:1.5px solid var(--white)}
.dots{top:552px;left:0;width:1200px;display:flex;justify-content:center;gap:8px}
.dots span{width:10px;height:10px;border-radius:50%;background:rgba(255,255,255,.55)}
.dots span:first-child{background:var(--white)}

/* intro */
.intro-title{left:110px;top:836px;font-size:24px;line-height:37px}
.photo{background:#8a8a8a}
.video-play{left:789px;top:1069px;width:52px;height:52px;border-radius:50%;background:var(--white);display:flex;align-items:center;justify-content:center}
.vertical-note{left:1052px;top:1440px;transform-origin:0 0;transform:rotate(-90deg);font-size:10.5px;letter-spacing:1.3px;color:var(--orange);text-transform:uppercase;white-space:nowrap}
.link-more{font-size:13px;font-weight:600;color:var(--lime-dark);text-transform:uppercase;display:flex;align-items:center;gap:8px}

/* services */
.services{top:1588px;left:0;width:1200px;height:615px;background:var(--pale)}
.section-title{font-size:38px}
.service-card{top:1779px;width:233px;height:339px;background:var(--white);text-align:center}
.service-card .photo{height:170px}
.service-card h3{font-size:14.5px;font-weight:600;margin-top:17px;text-transform:uppercase}
.service-card p{font-size:11.5px;line-height:21px;color:var(--text);padding:6px 14px 0}
.service-card .more{font-size:12.5px;font-weight:600;color:var(--lime-dark);margin-top:9px;text-transform:uppercase}
.slide-arrow{top:1938px;width:24px;height:24px}

/* about */
.about-title{left:655px;top:2329px;font-size:27px;line-height:45px}
.value-row{left:655px;top:2538px;display:flex;align-items:center;gap:10px;font-family:"Oswald",sans-serif;font-size:15px;color:var(--ink)}

/* projects */
.projects-bg{top:3200px;left:0;width:1200px;height:350px;background:linear-gradient(180deg,#ffffff 0%,#f1f1f1 50%,#ffffff 100%)}
.project-card{width:292px;height:393px;background:var(--white);box-shadow:0 2px 14px rgba(0,0,0,.12);padding:10px}
.project-card .photo{height:249px;display:flex}
.project-card .photo div{flex:1}
.project-card .tag{font-size:10.5px;font-weight:600;color:var(--lime-dark);margin:18px 0 0 6px;text-transform:uppercase}
.project-card h3{font-size:19px;font-weight:600;margin:8px 0 0 6px}
.project-card p{font-size:12px;line-height:22px;color:var(--text);margin:6px 0 0 6px}

/* testimonials */
.testimonials{top:3550px;left:0;width:1200px;height:542px;background:var(--lime)}
.rule-white{top:3658px;left:587px;width:26px;height:2px;background:var(--white)}
.quote-card{top:3739px;width:292px;height:266px;background:var(--white);padding:28px 16px 0 16px;overflow:visible}
.quote-head{display:flex;align-items:center;gap:12px;font-size:16px;font-weight:600}
.avatar{width:44px;height:44px;border-radius:50%;background:#b8a793}
.quote-card p{font-style:italic;font-size:13px;line-height:28px;color:#333;margin-top:16px}
.stars{color:var(--gold);font-size:22px;letter-spacing:1px;margin-top:2px}
.quote-mark{right:12px;bottom:-58px;font-family:"Oswald",sans-serif;font-size:120px;line-height:1;color:var(--lime-soft)}
.t-arrow{top:4025px;width:18px;height:14px}

/* contact */
.contact{top:4092px;left:0;width:1200px;height:641px;background:radial-gradient(circle at 30% 40%,#3d7a2a 0%,#245417 55%,#16380f 100%)}
.contact-box{top:4183px;left:270px;width:659px;height:469px;background:var(--lime)}
.contact-text{top:4300px;left:330px;width:540px;text-align:center;font-size:12px;line-height:25.5px;color:var(--white)}
.field{font-size:12.5px;color:var(--white);border-bottom:1px solid rgba(255,255,255,.7);padding-bottom:7px}
.submit{left:509px;top:4589px;width:177px;height:37px;border:1px solid var(--white);background:transparent}

/* footer */
.site-footer{top:4733px;left:0;width:1200px;height:347px;background:var(--footer)}
.footer-brand{left:108px;top:4838px;display:flex;flex-direction:column;align-items:center;gap:14px;width:190px;color:var(--white)}
.footer-brand .brand-mark{width:44px;height:44px;background:var(--white)}
.footer-brand span{font-weight:700;font-size:22px;line-height:27px;text-align:center;color:var(--white)}
.foot-col{top:4803px;color:var(--white)}
.foot-col h4{font-size:15px;font-weight:500;text-transform:uppercase;margin-bottom:16px;color:var(--white)}
.foot-col li{list-style:none;font-size:12px;line-height:26.5px;color:#e6e6e6;display:flex;gap:7px;align-items:center}
.foot-col li i{width:9px;height:9px;background:var(--white);display:inline-block}
.copyright{top:5040px;font-size:11.5px;color:#e6e6e6}
</style>
</head>
<body>

<header class="abs site-header">
  <div class="abs brand"><span class="brand-mark"></span><span class="brand-name">TOMLET BUILDERS</span></div>
  <div class="abs estimates">
    <span class="phone-dot"><svg width="16" height="16" viewBox="0 0 24 24"><path fill="#fff" d="M6.6 10.8a15.1 15.1 0 0 0 6.6 6.6l2.2-2.2c.3-.3.7-.4 1-.2 1.1.4 2.3.6 3.6.6.6 0 1 .4 1 1V20c0 .6-.4 1-1 1A17 17 0 0 1 3 4c0-.6.4-1 1-1h3.5c.6 0 1 .4 1 1 0 1.3.2 2.5.6 3.6.1.3 0 .7-.2 1z"/></svg></span>
    <div><small>FREE ESTIMATES</small><strong>888 888 8888</strong></div>
  </div>
  <div class="abs header-divider"></div>
  <span class="abs social-dot" style="left:989px"></span>
  <span class="abs social-dot" style="left:1023px"></span>
  <span class="abs social-dot" style="left:1058px"></span>
  <nav class="abs nav">
    <a class="active" style="left:395px">Home</a>
    <a style="left:517px">About Us</a>
    <a style="left:653px">Services</a>
    <a style="left:789px">Projects</a>
    <a style="left:909px">Blog</a>
    <a style="left:1038px">Contact Us</a>
  </nav>
</header>

<section class="abs hero" role="img" aria-label="Photo of a landscaped lawn with a curved brick garden path">
  <div class="abs hero-shade"></div>
</section>
<h1 class="abs center hero-title">TOMLET BUILDERS</h1>
<p class="abs center hero-sub">Lorem Ipsum is simply dummy text of the printing and typesetting industry.<br>Lorem Ipsum has been the industry's standard dummy text</p>
<a class="abs btn hero-btn">Get Started</a>
<span class="abs hero-arrow" style="left:60px"><svg width="27" height="27" viewBox="0 0 27 27"><path d="M15.5 8l-5 5.5 5 5.5" stroke="#fff" stroke-width="1.6" fill="none"/></svg></span>
<span class="abs hero-arrow" style="left:1110px"><svg width="27" height="27" viewBox="0 0 27 27"><path d="M11.5 8l5 5.5-5 5.5" stroke="#fff" stroke-width="1.6" fill="none"/></svg></span>
<div class="abs dots"><span></span><span></span><span></span><span></span></div>

<!-- introduction -->
<p class="abs eyebrow" style="left:110px;top:786px">Introduction</p>
<h2 class="abs heading intro-title">Section 1.10.33 of "the Garden Builder's<br>Notes", written by Arlo Venn<br>in 2019</h2>
<p class="abs body-copy" style="left:110px;top:963px;width:420px;font-size:11.5px">Lorem Ipsum is simply dummy text of the printing and typesetting industry. Lorem Ipsum has been the industry's standard dummy text ever since the 1500s, when an unknown printer</p>
<div class="abs photo" role="img" aria-label="Portrait of a smiling team member in a striped shirt" style="left:110px;top:1122px;width:300px;height:350px;background:linear-gradient(135deg,#4a4a4a,#7d8a9a 60%,#c8ccd4);box-shadow:0 4px 14px rgba(0,0,0,.25)"></div>
<div class="abs photo" role="img" aria-label="Photo of a gardener in orange cap mowing a lawn" style="left:625px;top:704px;width:462px;height:359px;background:linear-gradient(160deg,#4d7a2c,#7aa43c 50%,#d8822e 75%,#3c6224)"></div>
<div class="abs photo" role="img" aria-label="Video still of a red lawn mower on grass" style="left:667px;top:919px;width:300px;height:349px;background:linear-gradient(180deg,#c48a2a 0%,#6b8f2c 40%,#4f7a22 100%)"></div>
<span class="abs video-play"><svg width="18" height="18" viewBox="0 0 18 18"><path d="M5 3l10 6-10 6z" fill="#7a9e16"/></svg></span>
<p class="abs body-copy" style="left:671px;top:1295px;width:355px;font-size:11.5px">Lorem Ipsum is simply dummy text of the and typesetting industry. Lorem Ipsum has been the industry's standard dummy text ever since the 1500s, when an unknown printer took a galley of type and scrambled it to make a type specimen book. It has survived not only</p>
<a class="abs link-more" style="left:671px;top:1447px">Learn More <svg width="30" height="10" viewBox="0 0 30 10"><path d="M0 5h28M23 1l5 4-5 4" stroke="#7a9e16" stroke-width="1.6" fill="none"/></svg></a>
<span class="abs vertical-note">The standard Lorem Ipsum passage, used since</span>

<!-- services -->
<section class="abs services"></section>
<p class="abs eyebrow center" style="top:1674px">Our Services</p>
<h2 class="abs heading center section-title" style="top:1711px">What We Offer</h2>
<svg class="abs slide-arrow" style="left:67px" viewBox="0 0 24 24"><path d="M15 3l-8 9 8 9" stroke="#333" stroke-width="1.6" fill="none"/></svg>
<svg class="abs slide-arrow" style="left:1105px" viewBox="0 0 24 24"><path d="M9 3l8 9-8 9" stroke="#333" stroke-width="1.6" fill="none"/></svg>
<article class="abs service-card" style="left:110px"><div class="photo" role="img" aria-label="Photo of a landscaped flower garden" style="background:linear-gradient(180deg,#4a7a34,#7fb042 55%,#c8463e 80%,#e0b83c)"></div><h3>Landscaping</h3><p>Lorem ipsum dolor sur adipiscing elit, sed do eiod tempor incidnt ut labore et dolorena aliqua. Ut enim ad minim veniam, quis nostrud</p><div class="more">Learn More</div></article>
<article class="abs service-card" style="left:357px"><div class="photo" role="img" aria-label="Photo of a yellow mower on a striped lawn" style="background:linear-gradient(160deg,#3f7a1c,#6aa628 60%,#4f8a1e)"></div><h3>Mowing</h3><p>Lorem ipsum dolor sur adipiscing elit, sed do eiod tempor incidnt ut labore et dolorena aliqua. Ut enim ad minim veniam, quis nostrud</p><div class="more">Learn More</div></article>
<article class="abs service-card" style="left:605px"><div class="photo" role="img" aria-label="Photo of a concrete patio with outdoor furniture" style="background:linear-gradient(180deg,#5a7a3c,#8a8a80 55%,#b5b0a5)"></div><h3>Concrete</h3><p>Lorem ipsum dolor sur adipiscing elit, sed do eiod tempor incidnt ut labore et dolorena aliqua. Ut enim ad minim veniam, quis nostrud</p><div class="more">Learn More</div></article>
<article class="abs service-card" style="left:854px"><div class="photo" role="img" aria-label="Photo of a concrete sidewalk through grass" style="background:linear-gradient(90deg,#5f9a2a,#c9c4b4 45%,#c9c4b4 60%,#6aa530)"></div><h3>Sidewalks</h3><p>Lorem ipsum dolor sur adipiscing elit, sed do eiod tempor incidnt ut labore et dolorena aliqua. Ut enim ad minim veniam, quis nostrud</p><div class="more">Learn More</div></article>

<!-- about -->
<div class="abs photo" role="img" aria-label="Photo of a sunlit park lawn with trees and a curved path" style="left:110px;top:2288px;width:474px;height:388px;background:linear-gradient(150deg,#e9d88a 0%,#7aa23a 35%,#4c7f22 70%,#6fa62e)"></div>
<p class="abs eyebrow" style="left:655px;top:2283px">About Us</p>
<h2 class="abs heading about-title">Expect better than you are used to<br>when you work with us</h2>
<p class="abs body-copy" style="left:655px;top:2420px;width:434px;font-size:11.5px">At vero eos et accusamus et iusto odio dignissimos ducimus qui blanditiis praesentium voluptatum deleniti atque corrupti quos dolores et quas molestias excepturi sint occaecati cupiditate non provident, similique sunt in culpa qui officia deserunt mollitia animi</p>
<div class="abs value-row"><svg width="38" height="26" viewBox="0 0 38 26"><circle cx="10" cy="13" r="8" fill="none" stroke="#8db520" stroke-width="2"/><circle cx="28" cy="13" r="8" fill="none" stroke="#8db520" stroke-width="2"/><path d="M6 13l3 3 5-6" stroke="#8db520" stroke-width="2" fill="none"/></svg>Our Value</div>
<p class="abs body-copy" style="left:655px;top:2572px;width:434px;font-size:11.5px">At vero eos et accusamus et iusto odio dignissimos ducimus qui blanditiis praesentium voluptatum deleniti atque corrupti</p>
<a class="abs btn" style="left:655px;top:2643px;width:138px;height:37px">More About</a>

<!-- projects -->
<div class="abs projects-bg"></div>
<p class="abs eyebrow center" style="top:2823px">Our Work</p>
<h2 class="abs heading center section-title" style="top:2860px">Completed Projects</h2>
<article class="abs project-card" style="left:138px;top:2946px"><div class="photo" role="img" aria-label="Before and after photo of a side yard and garden bed"><div style="background:linear-gradient(180deg,#d8dde2,#8a8a70)"></div><div style="background:linear-gradient(180deg,#e4e6e8,#5d8f2a 75%,#c84a5a)"></div></div><div class="tag">Lorem Ipsum</div><h3>First Project Name</h3><p>Lorem Ipsum is simply dummy text of the printing and typeset industry.</p></article>
<article class="abs project-card" style="left:454px;top:2934px"><div class="photo" role="img" aria-label="Before and after photo of a bare soil path turned into a stone border"><div style="background:linear-gradient(180deg,#6e6454,#8a7a64)"></div><div style="background:linear-gradient(180deg,#5a8a2c,#c9c7c0 60%,#6b9a30)"></div></div><div class="tag">Lorem Ipsum</div><h3>Second Project Name</h3><p>Lorem Ipsum is simply dummy text of the printing and typeset industry.</p></article>
<article class="abs project-card" style="left:767px;top:2946px"><div class="photo" role="img" aria-label="Before and after photo of a red house front yard"><div style="background:linear-gradient(180deg,#6fa0d8,#8c2a2a 55%,#8a7a5a)"></div><div style="background:linear-gradient(180deg,#7fb0e4,#8c2a2a 50%,#5f9a2c)"></div></div><div class="tag">Lorem Ipsum</div><h3>Third Project Name</h3><p>Lorem Ipsum is simply dummy text of the printing and typeset industry.</p></article>
<a class="abs btn" style="left:501px;top:3376px;width:195px;height:38px">See More Projects</a>

<!-- testimonials -->
<section class="abs testimonials"></section>
<p class="abs eyebrow center on-green" style="top:3632px">Testimonials</p>
<div class="abs rule-white"></div>
<h2 class="abs heading center section-title on-green" style="top:3669px">Clients About Us</h2>
<article class="abs quote-card" style="left:144px"><div class="quote-head"><span class="avatar" role="img" aria-label="Client photo"></span>Maren in Westfield</div><p>Owen is an absolute gem. I feel lucky to have him working on my garden. He is a very hard worker and gives 120%. Can recommend him to anyone.</p><div class="stars">★★★★★</div><span class="abs quote-mark">”</span></article>
<article class="abs quote-card" style="left:454px"><div class="quote-head"><span class="avatar" role="img" aria-label="Client photo"></span>Dale Porter</div><p>Lorem ipsum dolor sit amet, consectetur adipiscing elit, sed do eiusmod tempor incididunt ut labore et dolore magna aliqua. Quis ipsum</p><div class="stars">★★★★★</div><span class="abs quote-mark">”</span></article>
<article class="abs quote-card" style="left:763px"><div class="quote-head"><span class="avatar" role="img" aria-label="Client photo"></span>Rita Vance</div><p>Lorem ipsum dolor sit amet, consectetur adipiscing elit, sed do eiusmod tempor incididunt ut labore et dolore magna aliqua. Quis ipsum</p><div class="stars">★★★★★</div><span class="abs quote-mark">”</span></article>
<svg class="abs t-arrow" style="left:146px" viewBox="0 0 18 14"><path d="M17 7H2M7 2L2 7l5 5" stroke="#e5efc6" stroke-width="1.4" fill="none"/></svg>
<svg class="abs t-arrow" style="left:1036px" viewBox="0 0 18 14"><path d="M1 7h15M11 2l5 5-5 5" stroke="#e5efc6" stroke-width="1.4" fill="none"/></svg>

<!-- contact -->
<section class="abs contact" role="img" aria-label="Background photo of dense green clover leaves"></section>
<div class="abs contact-box"></div>
<p class="abs eyebrow center on-green" style="top:4206px">Contact Us</p>
<h2 class="abs heading center section-title on-green" style="top:4245px;font-size:36px">How can we help you?</h2>
<p class="abs contact-text">Collaboration begins with a conversation. Whether you're interested in discussing a new project or simply wish to find out more about our services and what we can do for you, we are here to help. Send us a message below or call us at 888 888 8888</p>
<div class="abs field" style="left:359px;top:4400px;width:228px">Full Name*</div>
<div class="abs field" style="left:609px;top:4400px;width:228px">Email*</div>
<div class="abs field" style="left:359px;top:4451px;width:228px">Company*</div>
<div class="abs field" style="left:609px;top:4451px;width:228px">Phone*</div>
<div class="abs field" style="left:359px;top:4496px;width:478px;height:71px">Message*</div>
<a class="abs btn submit">Submit Request</a>

<!-- footer -->
<footer class="abs site-footer"></footer>
<div class="abs footer-brand"><span class="brand-mark"></span><span>TOMLET<br>BUILDERS</span></div>
<div class="abs foot-col" style="left:377px"><h4>Company</h4><ul><li>Home</li><li>About</li><li>Services</li><li>Work</li><li>Contact</li><li>Request a quote</li></ul></div>
<div class="abs foot-col" style="left:552px"><h4>Help</h4><ul><li>Contact Us</li><li>FAQ</li><li>Privacy Policy</li><li>Feedback</li><li>Sitemap</li></ul></div>
<div class="abs foot-col" style="left:714px"><h4>Contact Us</h4><ul>
  <li><svg width="10" height="12" viewBox="0 0 10 12"><path d="M5 0a4 4 0 0 0-4 4c0 3 4 8 4 8s4-5 4-8a4 4 0 0 0-4-4z" fill="#fff"/></svg>123 Avenue name, City name</li>
  <li style="padding-left:17px;margin-top:-6px">10150, United States</li>
  <li><svg width="10" height="10" viewBox="0 0 24 24"><path fill="#fff" d="M6.6 10.8a15.1 15.1 0 0 0 6.6 6.6l2.2-2.2c.3-.3.7-.4 1-.2 1.1.4 2.3.6 3.6.6.6 0 1 .4 1 1V20c0 .6-.4 1-1 1A17 17 0 0 1 3 4c0-.6.4-1 1-1h3.5c.6 0 1 .4 1 1 0 1.3.2 2.5.6 3.6.1.3 0 .7-.2 1z"/></svg>888 888 8888</li>
  <li><svg width="11" height="9" viewBox="0 0 11 9"><rect x=".5" y=".5" width="10" height="8" fill="none" stroke="#fff"/><path d="M.5 .5l5 4 5-4" stroke="#fff" fill="none"/></svg>info@tomletbuilders.com</li></ul></div>
<div class="abs foot-col" style="left:970px"><h4>Connect With Us</h4><ul><li><i></i>Our Page</li><li><i></i>Updates</li><li><i></i>Photos</li><li><i></i>Network</li></ul></div>
<p class="abs center copyright">Copyright © 2020 TOMLET BUILDERS. All Rights Reserved.</p>

</body>
</html>
```